2021 Summer Ads Hollis Bay Custom Homes

We need a re-design of our summer ad run for our customer, Hollis Bay Custom Homes. They are custom home builders in the mostly rural parts of West Virginia, USA. They are known for their "Forever Home" tagline. We'd like two designed ads with the main difference being just the custom home that's featured. These designs should be for a Zintrola banner like 300 x 250 and square ad like 250 x 250. For inspiration please visit the Hollis Bay Custom Homes website at www dot hollisbaycustomhomes dot com

Target Market(s)

consumers / new home shoppers

Industry/Entity Type

Consumer

Requirements
Must have
• HBCH logo
Price Lock Available!
Custom home pic
Learn more >
small CFRM logo mark

```html
<!DOCTYPE html>
<html lang="en">
<head>
<meta charset="utf-8">
<title>Hollis Bay Custom Homes – Summer Ad</title>
<link href="https://fonts.googleapis.com/css2?family=Montserrat:wght@500;700;800;900&display=swap" rel="stylesheet">
<style>
  :root {
    --navy: #1f2431;
    --red: #e3263a;
    --red-deep: #c81d30;
    --white: #ffffff;
    --sky: #dfe9ef;
    --foliage: #4f6b3a;
    --barn: #a8332b;
  }
  * { margin: 0; padding: 0; box-sizing: border-box; }
  html, body { width: 1200px; height: 1200px; overflow: hidden; background: var(--navy); }
  .ad {
    position: relative;
    width: 1200px;
    height: 1200px;
    overflow: hidden;
    background: var(--navy);
    font-family: "Montserrat", Arial, sans-serif;
    color: var(--white);
  }
  .home-photo {
    position: absolute;
    left: 0; top: 0;
    width: 1200px; height: 700px;
    background:
      linear-gradient(90deg, rgba(230,230,225,0.55) 0%, rgba(230,230,225,0.35) 45%, rgba(168,51,43,0.85) 55%, rgba(168,51,43,0.9) 100%) 0 300px / 100% 330px no-repeat,
      linear-gradient(180deg, var(--sky) 0%, #9fb28d 15%, var(--foliage) 40%, #707070 55%, #b9b4ab 100%);
  }
  .swoosh { position: absolute; left: 0; top: 0; width: 1200px; height: 1200px; }
  .brand {
    position: absolute;
    left: 45px; top: 690px;
    width: 450px;
    display: flex;
    align-items: center;
    gap: 18px;
  }
  .brand-mark {
    width: 46px; height: 46px;
    border-radius: 50%;
    background: var(--white);
    flex: none;
  }
  .brand-name {
    font-weight: 800;
    font-size: 40px;
    line-height: 1.05;
    letter-spacing: 1px;
    text-transform: uppercase;
    color: var(--white);
  }
  .headline {
    position: absolute;
    left: 45px; top: 818px;
    font-weight: 900;
    font-size: 72px;
    line-height: 82px;
    text-transform: uppercase;
  }
  .headline .accent { color: var(--red); display: block; }
  .headline .rest { color: var(--white); display: block; }
  .offer {
    position: absolute;
    left: 45px; top: 1088px;
    font-weight: 800;
    font-size: 42px;
    text-transform: uppercase;
    letter-spacing: 0.5px;
  }
  .partner {
    position: absolute;
    left: 870px; top: 870px;
    width: 260px;
    display: flex;
    flex-direction: column;
    align-items: flex-start;
  }
  .partner-name {
    font-weight: 900;
    font-size: 72px;
    line-height: 1;
    letter-spacing: 1px;
  }
  .partner-tagline {
    margin-top: 12px;
    font-weight: 500;
    font-size: 20px;
    line-height: 1.2;
  }
  .cta {
    position: absolute;
    left: 786px; top: 1050px;
    width: 390px; height: 99px;
    border-radius: 50px;
    background: var(--red);
    display: flex;
    align-items: center;
    justify-content: center;
    font-weight: 800;
    font-size: 36px;
    letter-spacing: 1px;
    text-transform: uppercase;
    color: var(--white);
    text-decoration: none;
  }
</style>
</head>
<body>
  <div class="ad">
    <div class="home-photo" role="img" aria-label="Photo of a white custom farmhouse with a red barn-style garage among green trees"></div>

    <svg class="swoosh" viewBox="0 0 1200 1200" aria-hidden="true">
      <path d="M0 600 C 320 555, 720 700, 1200 520 L1200 1200 L0 1200 Z" fill="var(--white)"/>
      <path d="M0 625 C 320 585, 720 725, 1200 548 L1200 1200 L0 1200 Z" fill="var(--red-deep)"/>
      <path d="M0 680 C 340 640, 740 770, 1200 620 L1200 1200 L0 1200 Z" fill="var(--navy)"/>
    </svg>

    <div class="brand">
      <span class="brand-mark"></span>
      <span class="brand-name">Hollis Bay<br>Custom Homes</span>
    </div>

    <h1 class="headline">
      <span class="accent">Start Building</span>
      <span class="rest">Your Forever</span>
      <span class="rest">Home Today!</span>
    </h1>

    <p class="offer">Price Lock Available!</p>

    <div class="partner">
      <span class="partner-name">CFRM</span>
      <span class="partner-tagline">Coalition of Fine<br>Residential Makers</span>
    </div>

    <a class="cta" href="#">Learn More</a>
  </div>
</body>
</html>
```